TK Stationery - Modern Contemporary

Develop modern template for Letterhead and Stationery (business card, letterhead, envelopes) using the TK Logo and Icon

Colors
0054AA
0677BA
7BADD7
CADEEF
E8F1F8
00AB8E
00BBA5
67D7C9
C6EFE9
E9F9F6
EE7325
F08F49
F5BC92
FAE3D3
FDF4ED
6B429C
8869AF
B7A5CE
E3DAEB
F3F0F8

```html
<!DOCTYPE html>
<html lang="en">
<head>
<meta charset="utf-8">
<title>TK Letterhead</title>
<link rel="stylesheet" href="https://fonts.googleapis.com/css2?family=Arimo&family=Questrial&family=Mulish:wght@700&display=swap">
<style>
  :root {
    --backdrop: #cdcccd;
    --paper: #ffffff;
    --navy: #252b45;
    --green: #3bb273;
    --ink: #555558;
    --signature: #4a4a4d;
  }
  * { margin: 0; padding: 0; box-sizing: border-box; }
  html, body { width: 1173px; height: 1200px; overflow: hidden; background: var(--backdrop); }
  .letterhead {
    position: absolute; left: 230px; top: 96px; width: 713px; height: 1009px;
    background: var(--paper); box-shadow: 2px 2px 4px rgba(0,0,0,.35);
  }
  .brand {
    position: absolute; top: 44px; left: 0; width: 100%; text-align: center;
    font-family: "Questrial", sans-serif; font-size: 40px; letter-spacing: 2px; color: var(--navy);
  }
  .salutation {
    position: absolute; left: 66px; top: 310px;
    font-family: "Mulish", sans-serif; font-weight: 700; font-size: 16px; color: var(--ink);
  }
  .letter-body {
    position: absolute; left: 64px; top: 357px; width: 590px;
    font-family: "Arimo", sans-serif; font-size: 11.2px; line-height: 14.7px; color: var(--ink);
  }
  .letter-body p { margin-bottom: 12.5px; }
  .letter-body span { display: block; white-space: nowrap; }
  .closing {
    position: absolute; left: 65px; top: 660px;
    font-family: "Mulish", sans-serif; font-weight: 700; font-size: 9.5px; color: var(--ink);
  }
  .signature {
    position: absolute; left: 64px; top: 702px; width: 117px; height: 35px;
    background: linear-gradient(90deg, #e6e6e7, #d4d4d6); border-radius: 3px;
  }
  .footer {
    position: absolute; left: 0; top: 950px; width: 100%;
    font-family: "Arimo", sans-serif; font-size: 12.3px; color: var(--navy); text-align: center;
  }
  .address { line-height: 14px; }
  .rule { width: 384px; height: 1px; background: var(--navy); margin: 3px auto 4px; }
  .contacts { display: flex; justify-content: center; align-items: center; gap: 11px; }
  .contact { display: flex; align-items: center; gap: 8px; }
  .contact svg { width: 9px; height: 9px; fill: var(--green); }
</style>
</head>
<body>
<main class="letterhead">
  <div class="brand">TK</div>

  <h1 class="salutation">Dear Mr. Smith,</h1>

  <section class="letter-body">
    <p>
      <span>Lorem ipsum dolor sit amet, consectetuer adipiscing elit, sed diam nonmmy nibh euismod tincidunt ut laor</span>
      <span>eet dolore magna aliquam erat volutpat. Ut wisi enim ad minim veniam, quis nostrud exerci tationmcorper</span>
      <span>suscipit lobortis nisl ut aliquip ex ea commodo consequat. Duis autem vel eum iriure dolor in hendrerit in</span>
      <span>vulputate velit esse molestie consequat, vel illum dolore eu feugiat</span>
    </p>
    <p>
      <span>Rorem ipsum dolor sit amet, consectetuer adipiscing elit, sed diam nonmmy nibh euismod tincidunt ut laor</span>
      <span>eet dolore magna aliquam erat volutpat. Ut wisi enim ad minim veniam, quis nostrud exerci tationmcorper</span>
      <span>suscipit lobortis nisl ut aliquip ex ea commodo consequat. Duis autem vel eum iriure dolor in hendrerit in</span>
      <span>vulputate velit esse molest</span>
    </p>
    <p>
      <span>Dorem ipsum dolor sit amet, consectetuer adipiscing elit, sed diam nonmmy nibh euismod tincidunt ut laor</span>
      <span>eet dolore magna aliquam erat volutpat. Ut wisi enim ad minim veniam, quis nostrud exerci tationmcorper</span>
      <span>suscipit lobortis nisl ut aliquip ex ea commodo consequat. Duis autem vel eum iriure dolor in hendrerit in</span>
      <span>suscipit lobortis nisl ut aliquip ex ea commodo consequat. Duis autem vel eum iriure dolor in hendrerit in</span>
      <span>vulputate velit esse molestie consequat, vel illum</span>
    </p>
    <p>
      <span>Sorem ipsum dolor sit amet, consectetuer adipiscing elit, sed diam nonmmy nibh euismod tincidunt ut laor</span>
      <span>eet dolore magna aliquam erat volutpat. Ut wisi enim ad minim veniam, quis nostrud exerci tationmcorper</span>
      <span>suscipit lobortis nisl ut aliquip ex ea commodo consequat. Duis autem vel eum iriure dolor in</span>
    </p>
  </section>

  <div class="closing">Sincerely,</div>
  <div class="signature" role="img" aria-label="Handwritten signature of the sender"></div>

  <footer class="footer">
    <div class="address">Your address, city, state, ZIP 0000</div>
    <div class="rule"></div>
    <div class="contacts">
      <span class="contact">
        <svg viewBox="0 0 10 10" aria-hidden="true"><path d="M2 0.5l1.6 0 0.7 2.3-1.1 0.8c0.5 1.2 1.3 2 2.5 2.5l0.8-1.1 2.3 0.7 0 1.6c0 0.6-0.5 1.1-1.1 1.1C4 8.4 1.1 5.6 0.9 1.6 0.9 1 1.4 0.5 2 0.5z"/></svg>
        123-456-2100
      </span>
      <span class="contact">
        <svg viewBox="0 0 10 10" aria-hidden="true"><path d="M0 2h10v6H0z M0.6 2.4 5 5.6 9.4 2.4" /></svg>
        info@tkstudio.com
      </span>
      <span class="contact">
        <svg viewBox="0 0 10 10" aria-hidden="true"><circle cx="5" cy="5" r="4.6"/></svg>
        www.tkstudio.com
      </span>
    </div>
  </footer>
</main>
</body>
</html>
```